Weightloss company needs Business Card

We want a business card that is clean and professional, yet portrays that we are a friendly, innovative, and versatile program designed to fit the needs of our clients.
I would like there to be 2 sides, one side having an appointment card, and the other side containing the logo and business information. There can be decorations on both sides. The logo is attached.

Target Market(s)

Men and women 40-60

Industry/Entity Type

Business

Contact Information for Business Card

Font styles to use
Sans Serif

Requirements
Must have
• The logo, space for business information
Nice to have
• The colors in the logo
Should not have
• No pictures of people or food

```html
<!DOCTYPE html>
<html lang="en">
<head>
<meta charset="UTF-8">
<title>Renewal Turn Business Card</title>
<link rel="stylesheet" href="https://fonts.googleapis.com/css2?family=Montserrat:wght@400;500;700;800&display=swap">
<style>
  :root {
    --bg: #232323;
    --card: #ffffff;
    --brand-red: #e81c37;
    --brand-blue: #3fb6e6;
    --ink: #111111;
    --rule: #222222;
    --on-red: #ffffff;
  }
  * { margin: 0; padding: 0; box-sizing: border-box; }
  html, body { width: 1200px; height: 900px; overflow: hidden; }
  body {
    background: var(--bg);
    font-family: "Montserrat", Arial, sans-serif;
    position: relative;
  }
  .card {
    position: absolute;
    width: 520px;
    height: 300px;
    border-radius: 22px;
    background: var(--card);
    overflow: hidden;
  }
  .card--appointment { left: 90px; top: 110px; }
  .card--front { left: 590px; top: 490px; }

  .brand {
    position: absolute;
    display: flex;
    align-items: center;
    gap: 10px;
    color: var(--brand-red);
    font-weight: 800;
    font-size: 26px;
    letter-spacing: 0.2px;
  }
  .brand__dot {
    width: 16px; height: 16px; border-radius: 50%;
    background: var(--brand-blue);
  }
  .card--appointment .brand { right: 34px; top: 40px; }
  .card--front .brand { right: 34px; top: 60px; }

  .appointment {
    position: absolute;
    left: 40px; top: 150px; right: 50px;
  }
  .appointment__title {
    color: var(--brand-red);
    font-size: 14px;
    font-weight: 500;
    letter-spacing: 0.3px;
    margin-bottom: 16px;
  }
  .appointment__field {
    display: flex;
    align-items: flex-end;
    gap: 10px;
    font-size: 15px;
    color: var(--ink);
    height: 36px;
  }
  .appointment__line {
    flex: 1;
    border-bottom: 1.5px solid var(--rule);
    margin-bottom: 4px;
  }

  .front-art { position: absolute; inset: 0; }

  .contact {
    position: absolute;
    left: 44px; top: 138px;
    color: var(--on-red);
  }
  .contact__name {
    color: var(--ink);
    font-weight: 800;
    font-size: 21px;
    letter-spacing: 0.3px;
  }
  .contact__role {
    font-size: 13px;
    font-weight: 500;
    margin-bottom: 8px;
  }
  .contact__address { font-size: 13px; line-height: 1.35; margin-bottom: 8px; }
  .contact__list { list-style: none; font-size: 13px; line-height: 1.5; }
  .contact__list li { display: flex; align-items: center; gap: 8px; }
  .contact__list svg { width: 12px; height: 12px; flex: none; }
</style>
</head>
<body>

<section class="card card--appointment" aria-label="Appointment card">
  <div class="brand"><span>Renewal Turn</span><span class="brand__dot"></span></div>
  <div class="appointment">
    <p class="appointment__title">APPOINTMENT</p>
    <div class="appointment__field"><span>Name:</span><span class="appointment__line"></span></div>
    <div class="appointment__field"><span>Date:</span><span class="appointment__line"></span></div>
    <div class="appointment__field"><span>Time:</span><span class="appointment__line"></span></div>
  </div>
</section>

<section class="card card--front" aria-label="Business card front">
  <svg class="front-art" viewBox="0 0 520 300" aria-hidden="true">
    <circle cx="186" cy="300" r="228" fill="#111111" stroke="#3fb6e6" stroke-width="2"/>
    <circle cx="168" cy="302" r="218" fill="#e81c37"/>
  </svg>
  <div class="brand"><span>Renewal Turn</span><span class="brand__dot"></span></div>
  <div class="contact">
    <p class="contact__name">MARLO FENWICK</p>
    <p class="contact__role">DIRECTOR</p>
    <p class="contact__address">Harbor Lane, 21430<br>Westfield, Coastland</p>
    <ul class="contact__list">
      <li><svg viewBox="0 0 24 24"><path fill="#111" d="M6.6 10.8a15 15 0 0 0 6.6 6.6l2.2-2.2c.3-.3.7-.4 1-.2 1.1.4 2.3.6 3.6.6.6 0 1 .4 1 1V20c0 .6-.4 1-1 1A17 17 0 0 1 3 4c0-.6.4-1 1-1h3.5c.6 0 1 .4 1 1 0 1.3.2 2.5.6 3.6.1.3 0 .7-.2 1z"/></svg>+330 2471-3382</li>
      <li><svg viewBox="0 0 24 24"><rect x="2" y="5" width="20" height="14" rx="1.5" fill="none" stroke="#111" stroke-width="2.2"/><path d="M3 6l9 7 9-7" fill="none" stroke="#111" stroke-width="2.2"/></svg>info@renewalturn.com</li>
      <li><svg viewBox="0 0 24 24"><circle cx="12" cy="12" r="9.5" fill="none" stroke="#111" stroke-width="2.2"/><path d="M2.5 12h19M12 2.5c3 3 3 16 0 19M12 2.5c-3 3-3 16 0 19" fill="none" stroke="#111" stroke-width="2"/></svg>www.renewalturn.com</li>
    </ul>
  </div>
</section>

</body>
</html>
```